Personal Care and Home care ingredients Brochure

We need a flyer or brochure of the of chemicals we distribute for the manufacturing of personal care products such as shampoos, liquid soaps, creams, lotions, conditioners, hand sanitizer, Hair Jellys, etc and for Home care products such as, liquid soaps, desinfectants, cleaners, stain removers,etc.
The idea is to send this pdf brochure via email and companies feel very confortable with the impression it gives. We want to call attention.
Target Market(s)
Companies that manufactures cosmetics, personal care products and home care products.
Font styles to use
Colors
Designer to choose colors to be used in the design.
Requirements
Must have
- Images that refers to the skin, hair, cleaning, washing

```html
<!DOCTYPE html>
<html lang="es">
<head>
<meta charset="UTF-8">
<title>Sulfonatos de Ester Metilico (MES) – Folleto</title>
<link href="https://fonts.googleapis.com/css2?family=Lato:wght@400;700;900&display=swap" rel="stylesheet">
<style>
  :root{
    --backdrop:#e2e2e2;
    --page:#f1f1f1;
    --green:#2f9e7d;
    --green-light:#5bb898;
    --green-dark:#1f7a60;
    --navy:#1f2a36;
    --ink:#1d1f22;
    --photo-a:#b9cfae;
    --photo-b:#e6dde2;
    --photo-c:#f2efe9;
  }
  *{margin:0;padding:0;box-sizing:border-box}
  html,body{width:1200px;height:700px;overflow:hidden;background:var(--backdrop);font-family:'Lato',sans-serif}
  .spread{
    position:absolute;left:60px;top:80px;width:1080px;height:540px;
    display:flex;background:var(--page);
  }
  .page{position:relative;width:540px;height:540px;overflow:hidden}
  .page--photo{
    background:linear-gradient(135deg,var(--photo-a) 0%,var(--photo-b) 45%,var(--photo-c) 75%,var(--photo-a) 100%);
  }
  .page--text{background:var(--page)}
  .page-art{position:absolute;inset:0;width:100%;height:100%}
  .content{position:absolute;left:52px;top:170px;width:400px;color:var(--ink)}
  .content__title{color:var(--green);font-weight:900;font-size:24px;line-height:1.2;margin-bottom:18px}
  .content__text{font-weight:700;font-size:13px;line-height:1.45;margin-bottom:14px}
  .brand{
    position:absolute;right:40px;bottom:110px;display:flex;align-items:center;gap:8px;
    color:var(--navy);font-weight:900;font-size:16px;letter-spacing:1px
  }
  .brand__mark{width:14px;height:14px;background:var(--green)}
</style>
</head>
<body>
  <div class="spread">
    <section class="page page--photo" role="img" aria-label="Fotografía de una clienta eligiendo un producto de cuidado personal en un pasillo de supermercado"></section>
    <section class="page page--text">
      <svg class="page-art" viewBox="0 0 540 540" aria-hidden="true">
        <polygon points="250,0 410,0 370,60 260,60" fill="var(--green-light)"/>
        <polygon points="370,60 410,0 470,0 420,80" fill="var(--green-dark)"/>
        <polygon points="420,80 470,0 540,0 540,20 470,80" fill="var(--green)"/>
        <polygon points="0,540 0,470 150,470 200,540" fill="var(--navy)"/>
        <polygon points="0,470 0,440 170,440 150,470" fill="var(--green)"/>
      </svg>
      <div class="content">
        <h1 class="content__title">Sulfonatos de Ester Metilico (MES)</h1>
        <p class="content__text">El VERDASULF es un surfactante ionico utilizado como ingrediente activo en detergentes.</p>
        <p class="content__text">Su principal uso es como substituto del surfactante universalmente utilizado, LAS o alquil sulfonatos lineales en las formulas de los detergentes. Esta hecho de recursos naturales renovables, lo cual le da un excelente biodegradabilidad, y muestra una mejor detergencia y tolerancia a la dureza durante el lavado.</p>
      </div>
      <div class="brand"><span class="brand__mark"></span>NEXA QUIMICA</div>
    </section>
  </div>
</body>
</html>
```